New Modern High end Gin Design

We are looking for a new design for our current gin. The gin is named Lamp Heron Gin. We are looking for the bottle to be blue and the lettering to be gold. Please add the design on the bottle. the picture of the current bottle is in the uploaded files. we will not be using the same bottle. See photo attached with bottle type we would like to use. We would also like to make the lamp heron imaged embossed

Font styles to use
Decorative

Colors
0054AA
0677BA
7BADD7
CADEEF
E8F1F8
0094D4
00A9DD
6FCCEA
C7EBF8
E9F6FB
FFC000
F8CF3A
FAE287
FDF2CF
FEFAEE

Requirements
Must have
• blue bottle
Nice to have
• ridges in the bottle

```html
<!DOCTYPE html>
<html lang="en">
<head>
<meta charset="utf-8">
<title>Lamp Heron Gin – Label</title>
<link rel="stylesheet" href="https://fonts.googleapis.com/css2?family=Abril+Fatface&family=Alegreya+Sans:wght@800&display=swap">
<style>
  :root {
    --bg-blue: #1d578d;
    --gold-light: #f8e28f;
    --gold-mid: #d8bd5c;
    --gold-deep: #b08f2a;
    --gin-blue: #93c8ee;
  }
  html, body {
    margin: 0;
    padding: 0;
    width: 1200px;
    height: 1000px;
    overflow: hidden;
    background: var(--bg-blue);
  }
  .label {
    display: block;
    width: 1200px;
    height: 1000px;
  }
  .brand-word {
    font-family: "Abril Fatface", serif;
    font-size: 118px;
  }
  .gin-word {
    font-family: "Abril Fatface", serif;
    font-size: 76px;
    fill: var(--gin-blue);
  }
  .side-note {
    font-family: "Alegreya Sans", sans-serif;
    font-weight: 800;
    font-size: 17px;
    letter-spacing: 3px;
  }
  .arc-text {
    font-family: "Alegreya Sans", sans-serif;
    font-weight: 800;
    font-size: 25px;
    letter-spacing: 4px;
  }
  .measure {
    font-family: "Alegreya Sans", sans-serif;
    font-weight: 800;
  }
  .swoosh { fill: none; stroke: url(#goldSweep); stroke-linecap: round; }
</style>
</head>
<body>
<svg class="label" viewBox="0 0 1200 1000" xmlns="http://www.w3.org/2000/svg">
  <defs>
    <linearGradient id="goldSweep" gradientUnits="userSpaceOnUse" x1="350" y1="0" x2="865" y2="0">
      <stop offset="0" stop-color="var(--gold-light)"/>
      <stop offset="0.55" stop-color="var(--gold-mid)"/>
      <stop offset="1" stop-color="var(--gold-deep)"/>
    </linearGradient>
    <linearGradient id="sceneTone" x1="0" y1="0" x2="1" y2="1">
      <stop offset="0" stop-color="#d2b24e"/>
      <stop offset="1" stop-color="#a8882a"/>
    </linearGradient>
    <path id="wavePath" d="M355,556 C440,572 520,640 606,664 C690,650 770,585 852,552"/>
  </defs>

  <!-- header rule -->
  <g class="header-rule" fill="url(#goldSweep)">
    <polygon points="357,307 703,307 691,314 357,314"/>
    <rect x="840" y="307" width="13" height="7.5"/>
  </g>

  <!-- cart scene artwork -->
  <g class="scene-art" role="img" aria-label="Engraved illustration of two workers pumping a rail hand cart">
    <rect x="669" y="300" width="191" height="124" rx="6" fill="url(#sceneTone)" opacity="0.85"/>
    <rect x="780" y="418" width="80" height="46" rx="6" fill="url(#sceneTone)" opacity="0.85"/>
  </g>

  <!-- ornament placeholders -->
  <rect x="351" y="432" width="83" height="34" rx="14" fill="var(--gold-light)" opacity="0.22"
        role="img" aria-label="Scroll flourish ornament"/>
  <rect x="471" y="540" width="48" height="31" rx="14" fill="var(--gold-light)" opacity="0.22"
        role="img" aria-label="Scroll flourish ornament"/>

  <!-- brand name -->
  <g class="brand-name" fill="url(#goldSweep)">
    <text class="brand-word" x="357" y="426" textLength="303" lengthAdjust="spacingAndGlyphs">LAMP</text>
    <text class="brand-word" x="443" y="533" textLength="322" lengthAdjust="spacingAndGlyphs">HERON</text>
  </g>
  <text class="gin-word" x="530" y="600" textLength="142" lengthAdjust="spacingAndGlyphs">GIN</text>

  <!-- side notes -->
  <g class="side-notes">
    <text class="side-note" x="386" y="487" text-anchor="middle" fill="var(--gold-light)">SMALL</text>
    <text class="side-note" x="386" y="506" text-anchor="middle" fill="var(--gold-light)">BATCH</text>
    <text class="side-note" x="822" y="489" text-anchor="middle" fill="var(--gold-deep)">MOUNT</text>
    <text class="side-note" x="822" y="508" text-anchor="middle" fill="var(--gold-deep)">WREN</text>
  </g>

  <!-- wave bands -->
  <g class="wave-bands">
    <path class="swoosh" stroke-width="4" d="M347,523 C440,530 480,575 518,599 C545,613 570,619 592,621"/>
    <path class="swoosh" stroke-width="4" d="M619,621 C660,612 720,580 770,548 C800,530 830,524 861,523"/>
    <path class="swoosh" stroke-width="3.5" d="M350,572 C430,576 480,630 534,664"/>
    <path class="swoosh" stroke-width="3.5" d="M674,664 C730,635 790,578 857,572"/>
    <path class="swoosh" stroke-width="1.2" d="M353,585 C400,598 440,610 462,622"/>
    <path class="swoosh" stroke-width="1.2" d="M458,641 C490,650 510,660 519,665"/>
    <path class="swoosh" stroke-width="1.2" d="M854,585 C810,598 795,605 780,619"/>
    <path class="swoosh" stroke-width="1.2" d="M690,665 C710,660 730,650 747,641"/>
    <g fill="var(--gold-mid)">
      <circle cx="597" cy="617" r="1.3"/>
      <circle cx="603" cy="617" r="1.3"/>
      <circle cx="609" cy="617" r="1.3"/>
    </g>
  </g>

  <!-- distillery arc -->
  <text class="arc-text" fill="url(#goldSweep)">
    <textPath href="#wavePath" startOffset="4" textLength="525" lengthAdjust="spacing">LANTERN BEND DISTILLERY</textPath>
  </text>

  <!-- measures -->
  <g class="measures">
    <text class="measure" x="369" y="648" font-size="12" fill="var(--gold-light)">VOL</text>
    <text class="measure" x="398" y="648" font-size="21" fill="var(--gold-light)">40%</text>
    <text class="measure" x="757" y="647" font-size="21" fill="var(--gold-deep)">750</text>
    <text class="measure" x="800" y="647" font-size="11" fill="var(--gold-deep)">ML</text>
  </g>
</svg>
</body>
</html>
```